Banner Ad Design Project

I require banner ad designs with the below wording.

1. Join Today and Make Money Tomorrow. Unlimited Income. Click Here Now

2. I lost my job. Now I Make Over $5,000 Per Week From Home. You Can Too. Free Info, Apply Now

I require sizes: 300x250 and 728x90 and 468x60 and 120x240

The design should communicate legitimate, accredited, online business.

Industry/Entity Type

Business

Requirements
Should not have
• Creative attributes to avoid*
Phone numbers in creative
Creative with no click buttons
Interactive creative
Brand messaging with no call to action
Creative with long looping times

```html
<!DOCTYPE html>
<html lang="en">
<head>
<meta charset="utf-8">
<title>Work From Home – Banner Set</title>
<link href="https://fonts.googleapis.com/css2?family=Roboto+Condensed:wght@400;700&display=swap" rel="stylesheet">
<style>
  :root{
    --stage-top:#7b7b7b;
    --stage-bottom:#020202;
    --magenta:#cc1652;
    --magenta-deep:#a30d3f;
    --magenta-edge:#8c0a35;
    --white:#ffffff;
    --gold:#ffe640;
    --gold-shade:#c45a00;
    --photo-light:#f1efee;
    --photo-mid:#d9cfc8;
    --photo-dark:#3a3032;
  }
  *{box-sizing:border-box;margin:0;padding:0}
  html,body{width:1200px;height:848px;overflow:hidden}
  body{
    position:relative;
    background:linear-gradient(180deg,var(--stage-top) 0%,#3c3c3c 55%,var(--stage-bottom) 100%);
    font-family:"Roboto Condensed",Arial Narrow,sans-serif;
  }
  .banner{position:absolute;overflow:hidden;box-shadow:0 2px 6px rgba(0,0,0,.35)}
  .banner svg.shapes{position:absolute;inset:0;width:100%;height:100%}
  .photo{
    position:absolute;
    background:linear-gradient(135deg,var(--photo-light) 0%,var(--photo-mid) 55%,var(--photo-dark) 100%);
  }
  .line{position:absolute;left:0;width:100%;text-align:center;color:var(--white);line-height:1;white-space:nowrap}
  .headline{font-weight:400}
  .amount{
    font-weight:700;color:var(--gold);
    text-shadow:1px 1px 0 var(--gold-shade),-1px 0 0 var(--gold-shade),0 -1px 0 var(--gold-shade),0 2px 2px rgba(0,0,0,.3);
  }
  .cta{color:var(--magenta);font-weight:400}

  /* 728x90 leaderboard */
  .leaderboard{left:108px;top:96px;width:947px;height:117px}
  .leaderboard .photo{left:0;top:0;width:260px;height:117px}
  .leaderboard .message{position:absolute;left:220px;width:300px;top:0;height:117px}
  .leaderboard .headline{top:11px;font-size:26px}
  .leaderboard .amount{top:44px;font-size:35px}
  .leaderboard .home{top:80px;font-size:24px}
  .leaderboard .offer{position:absolute;left:600px;width:300px;top:0;height:117px}
  .leaderboard .cta{font-size:33px}
  .leaderboard .cta.first{top:17px}
  .leaderboard .cta.second{top:60px}

  /* 468x60 banner */
  .full-banner{left:275px;top:258px;width:610px;height:78px}
  .full-banner .photo{left:0;top:0;width:170px;height:78px}
  .full-banner .message{position:absolute;left:145px;width:255px;top:0;height:78px}
  .full-banner .headline{top:7px;font-size:18px}
  .full-banner .amount{top:28px;font-size:26px}
  .full-banner .home{top:56px;font-size:17px}
  .full-banner .offer{position:absolute;left:405px;width:185px;top:0;height:78px}
  .full-banner .cta{font-size:18px}
  .full-banner .cta.first{top:15px}
  .full-banner .cta.second{top:42px}

  /* 300x250 rectangle */
  .rectangle{left:236px;top:439px;width:390px;height:325px}
  .rectangle .headline{top:157px;font-size:27px}
  .rectangle .amount{top:190px;font-size:39px}
  .rectangle .home{top:235px;font-size:25px}
  .rectangle .cta{top:286px;font-size:25px}

  /* 120x240 skyscraper */
  .skyscraper{left:729px;top:439px;width:156px;height:312px}
  .skyscraper .headline{font-size:19px}
  .skyscraper .l1{top:124px}
  .skyscraper .l2{top:153px}
  .skyscraper .amount{font-size:30px}
  .skyscraper .a1{top:180px}
  .skyscraper .a2{top:211px}
  .skyscraper .home{top:244px;font-size:19px}
  .skyscraper .apply-button{
    position:absolute;left:7px;top:278px;width:142px;height:25px;border-radius:13px;
    background:var(--white);color:var(--magenta);font-weight:700;font-size:13px;
    display:flex;align-items:center;justify-content:center;white-space:nowrap;
  }
</style>
</head>
<body>

<!-- 728x90 -->
<div class="banner leaderboard">
  <div class="photo" role="img" aria-label="Photo of a joyful businesswoman in a dark suit raising her arms"></div>
  <svg class="shapes" viewBox="0 0 947 117" preserveAspectRatio="none" aria-hidden="true">
    <defs>
      <linearGradient id="lbMagenta" x1="0" y1="0" x2="1" y2="1">
        <stop offset="0" stop-color="var(--magenta)"/>
        <stop offset="1" stop-color="var(--magenta-deep)"/>
      </linearGradient>
    </defs>
    <path d="M196 0 C170 40 178 88 222 117 L590 117 L590 0 Z" fill="var(--magenta-edge)"/>
    <path d="M208 0 C184 40 192 88 236 117 L590 117 L590 0 Z" fill="url(#lbMagenta)"/>
    <path d="M560 0 L572 117 L590 117 L580 0 Z" fill="var(--magenta-edge)"/>
    <path d="M576 0 L947 0 L947 117 L588 117 Z" fill="var(--white)"/>
    <path d="M924 0 L947 0 L947 117 L924 117 L906 58 Z" fill="var(--magenta)"/>
  </svg>
  <div class="message">
    <div class="line headline">I lost my job Now I Make Over</div>
    <div class="line amount">$5,000 Per Week</div>
    <div class="line home">From Home</div>
  </div>
  <div class="offer">
    <div class="line cta first">You Can Too</div>
    <div class="line cta second">Free Info, Apply Now</div>
  </div>
</div>

<!-- 468x60 -->
<div class="banner full-banner">
  <div class="photo" role="img" aria-label="Photo of a joyful businesswoman in a dark suit raising her arms"></div>
  <svg class="shapes" viewBox="0 0 610 78" preserveAspectRatio="none" aria-hidden="true">
    <defs>
      <linearGradient id="fbMagenta" x1="0" y1="0" x2="1" y2="1">
        <stop offset="0" stop-color="var(--magenta)"/>
        <stop offset="1" stop-color="var(--magenta-deep)"/>
      </linearGradient>
    </defs>
    <path d="M138 0 C120 28 124 58 152 78 L405 78 L405 0 Z" fill="var(--magenta-edge)"/>
    <path d="M146 0 C129 28 133 58 161 78 L405 78 L405 0 Z" fill="url(#fbMagenta)"/>
    <path d="M404 0 L610 0 L610 78 L410 78 Z" fill="var(--white)"/>
    <path d="M594 0 L610 0 L610 78 L594 78 L582 39 Z" fill="var(--magenta)"/>
  </svg>
  <div class="message">
    <div class="line headline">I lost my job Now I Make Over</div>
    <div class="line amount">$5,000 Per Week</div>
    <div class="line home">From Home</div>
  </div>
  <div class="offer">
    <div class="line cta first">You Can Too</div>
    <div class="line cta second">Free Info, Apply Now</div>
  </div>
</div>

<!-- 300x250 -->
<div class="banner rectangle">
  <svg class="shapes" viewBox="0 0 390 325" preserveAspectRatio="none" aria-hidden="true">
    <defs>
      <radialGradient id="rcMagenta" cx="0.4" cy="0.55" r="0.7">
        <stop offset="0" stop-color="var(--magenta)"/>
        <stop offset="1" stop-color="var(--magenta-deep)"/>
      </radialGradient>
    </defs>
    <rect width="390" height="325" fill="url(#rcMagenta)"/>
    <path d="M44 0 C40 60 150 124 390 132 L390 0 Z" fill="var(--magenta-edge)"/>
    <path d="M0 282 C90 268 300 264 390 286 L390 325 L0 325 Z" fill="var(--white)"/>
  </svg>
  <div class="photo" role="img" aria-label="Photo of a joyful businesswoman in a dark suit raising her arms"
       style="left:0;top:0;width:390px;height:128px;clip-path:path('M52 0 C48 56 156 118 390 124 L390 0 Z')"></div>
  <div class="line headline">I lost my job Now I Make Over</div>
  <div class="line amount">$5,000 Per Week</div>
  <div class="line home">From Home</div>
  <div class="line cta">You Can Too Free Info, Apply Now</div>
</div>

<!-- 120x240 -->
<div class="banner skyscraper">
  <svg class="shapes" viewBox="0 0 156 312" preserveAspectRatio="none" aria-hidden="true">
    <defs>
      <linearGradient id="skMagenta" x1="0" y1="0" x2="0" y2="1">
        <stop offset="0" stop-color="var(--magenta)"/>
        <stop offset="1" stop-color="var(--magenta-deep)"/>
      </linearGradient>
    </defs>
    <rect width="156" height="312" fill="url(#skMagenta)"/>
    <path d="M0 40 C40 68 100 82 156 84 L156 0 L0 0 Z" fill="var(--magenta-edge)"/>
  </svg>
  <div class="photo" role="img" aria-label="Photo of a joyful businesswoman in a dark suit raising her arms"
       style="left:0;top:0;width:156px;height:82px;clip-path:path('M0 34 C40 62 100 76 156 78 L156 0 L0 0 Z')"></div>
  <div class="line headline l1">I lost my job</div>
  <div class="line headline l2">Now I Make Over</div>
  <div class="line amount a1">$5,000</div>
  <div class="line amount a2">Per Week</div>
  <div class="line home">From Home</div>
  <div class="apply-button">Free Info, Apply Now</div>
</div>

</body>
</html>
```